Quorva - corporate Business Card

We need a good look and innovative business card for a new start up company based in Los Angeles called "Quorva". We are in a payment business, including payment card, app, and ewallet. We are expert in online payment and Card not present (CNP) transaction.
We need an innovative, modern business card.

Our logo font is Aero Matics

Target Market(s)

Startup - Bank - Online Payment - Card Manufacturing

Industry/Entity Type

Startup

Contact Information for Business Card

phone: 555 014 7396 - Address: 4172 Marlowe blvd, Brenmoor City, OR 90299

Requirements
Must have
• Message: innovative, professional, expert, high tech, trust, online payment expert, security
Nice to have
• no comment
Should not have
• no Comment

```html
<!DOCTYPE html>
<html lang="en">
<head>
<meta charset="utf-8">
<title>Quorva – Business Card</title>
<link rel="stylesheet" href="https://fonts.googleapis.com/css2?family=Catamaran:wght@400;500;700&display=swap">
<style>
  :root {
    --brand-red: #b91f30;
    --card-white: #fdfdfd;
    --card-black: #050505;
    --ink: #1b1b1b;
    --backdrop: #e9e7e5;
    --card-radius: 20px;
  }
  html, body {
    margin: 0;
    padding: 0;
    width: 1200px;
    height: 900px;
    overflow: hidden;
    background: var(--backdrop);
    font-family: "Catamaran", sans-serif;
  }
  .stage {
    position: relative;
    width: 1200px;
    height: 900px;
  }
  .card {
    position: absolute;
    border-radius: var(--card-radius);
    box-shadow: 0 6px 18px rgba(0,0,0,0.12);
  }
  .card--front {
    left: 239px;
    top: 60px;
    width: 555px;
    height: 344px;
    background: var(--card-white);
    text-align: center;
    color: var(--ink);
  }
  .card--back {
    left: 458px;
    top: 518px;
    width: 558px;
    height: 344px;
    background: var(--card-black);
  }
  .wordmark {
    position: absolute;
    left: 0;
    right: 0;
    top: 40px;
    margin: 0;
    font-weight: 700;
    font-size: 78px;
    line-height: 1;
    letter-spacing: 1px;
    color: var(--brand-red);
  }
  .person {
    position: absolute;
    left: 0;
    right: 0;
    top: 186px;
  }
  .person__name {
    margin: 0;
    font-weight: 700;
    font-size: 30px;
    line-height: 1;
    color: var(--brand-red);
  }
  .person__role {
    margin: 6px 0 0;
    font-weight: 500;
    font-size: 17px;
    line-height: 1;
  }
  .contact {
    position: absolute;
    left: 0;
    right: 0;
    top: 253px;
    font-size: 16.5px;
    font-weight: 500;
    line-height: 1;
  }
  .contact__line { margin: 0 0 17px; }
  .contact__divider {
    display: inline-block;
    width: 2px;
    height: 19px;
    margin: 0 6px;
    vertical-align: -4px;
    background: var(--brand-red);
  }
  .back-mark {
    position: absolute;
    left: 117px;
    top: 123px;
    display: flex;
    align-items: center;
    gap: 14px;
  }
  .back-mark__dot {
    width: 96px;
    height: 96px;
    border-radius: 50%;
    background: var(--brand-red);
  }
  .back-mark__name {
    font-weight: 700;
    font-size: 68px;
    line-height: 1;
    letter-spacing: 1px;
    color: var(--brand-red);
  }
</style>
</head>
<body>
<main class="stage">
  <section class="card card--front">
    <h1 class="wordmark">quorva</h1>
    <div class="person">
      <p class="person__name">Daniel Reyes</p>
      <p class="person__role">Director</p>
    </div>
    <div class="contact">
      <p class="contact__line">555 014 7396<span class="contact__divider"></span>www.quorva.com</p>
      <p class="contact__line">4172 Marlowe blvd, Brenmoor City, OR 90299</p>
    </div>
  </section>
  <section class="card card--back">
    <div class="back-mark">
      <span class="back-mark__dot"></span>
      <span class="back-mark__name">quorva</span>
    </div>
  </section>
</main>
</body>
</html>
```